Leadership Training Business Needs a business card design

We need a business card designed for our company based in Auckland, New Zealand called Harbour Pathway Advisors. We conduct a variety of residential programmes that provide for differnet management levels. These programmes are designed to familiarise managers with important leadership concepts and techniques. This learning is reinforced through the provision of real workplace feedback and the use of action learning opportunities (experiential exercises) to develop the participants' leadership skills and potential. We would like to add our tag line which is:
Inspires Direction - Instils Values - Delivers Results
We would like the card to be a white background but would consider a different background colour on the back. Possibly include the following words on the back:
- Organisational Development
- Positive Cultural Change
- Leadership Programmes
- Practical Development "Tools"
- Crew Rhythm Inventory
- 360o degree Assessments
- Strengths Based Training
- Coaching and Mentoring

• Company Name, logo, contact details, website address and email.
• Persons name and their title

```html
<!DOCTYPE html>
<html lang="en">
<head>
<meta charset="utf-8">
<title>Harbour Pathway Advisors – Business Card</title>
<link rel="stylesheet" href="https://fonts.googleapis.com/css2?family=Open+Sans:ital,wght@0,400;0,600;1,400&family=Rubik:wght@400;700&display=swap">
<style>
  :root {
    --page-bg: #e9e7e3;
    --card-white: #f4f5f6;
    --card-blue: #2f4597;
    --ink-dark: #1d1d22;
    --ink-blue: #2f4597;
    --ink-grey: #3a3a40;
    --rule-grey: #c9cbd0;
    --mark-light: #d6d9e6;
    --mark-colour: #8cbf3a;
    --white: #ffffff;
  }
  * { box-sizing: border-box; margin: 0; padding: 0; }
  html, body {
    width: 1200px; height: 880px; overflow: hidden;
    background: var(--page-bg);
    font-family: "Open Sans", Arial, sans-serif;
  }
  .canvas {
    position: relative; width: 1200px; height: 880px;
  }
  .card {
    position: absolute; left: 250px; width: 700px; height: 400px;
    border-radius: 4px;
    box-shadow: 0 6px 18px rgba(0,0,0,0.18);
    overflow: hidden;
  }
  /* ---------- front ---------- */
  .card-front { top: 30px; background: var(--card-white); }
  .brand {
    position: absolute; left: 60px; top: 120px;
    display: flex; flex-direction: column; align-items: flex-start;
  }
  .brand-dot {
    width: 58px; height: 58px; border-radius: 50%;
    background: var(--mark-colour); margin: 0 0 14px 70px;
  }
  .brand-name {
    font-size: 25px; font-weight: 400; color: var(--ink-dark);
    line-height: 1.1;
  }
  .brand-line {
    font-size: 25px; font-weight: 400; color: var(--ink-blue);
    line-height: 1.15;
  }
  .person {
    position: absolute; right: 48px; top: 92px; text-align: right;
  }
  .person-name {
    font-family: "Rubik", Arial, sans-serif;
    font-weight: 700; font-size: 40px; color: var(--ink-blue); line-height: 1;
  }
  .person-title {
    font-size: 17px; color: var(--ink-dark); margin-top: 4px;
  }
  .rule {
    position: absolute; right: 48px; width: 300px; height: 1px;
    background: var(--rule-grey);
  }
  .rule-top { top: 172px; }
  .rule-mid { top: 300px; }
  .contact-list {
    position: absolute; right: 48px; list-style: none;
    font-size: 17px; color: var(--ink-dark); line-height: 28px;
  }
  .contact-list li {
    display: flex; justify-content: flex-end; align-items: center; gap: 10px;
  }
  .contact-lines { top: 182px; }
  .address-lines { top: 312px; }
  .address-lines li { align-items: flex-start; }
  .icon { width: 14px; height: 14px; flex: none; fill: var(--ink-blue); }
  .address-block { text-align: right; }
  /* ---------- back ---------- */
  .card-back { top: 450px; background: var(--card-blue); color: var(--white); }
  .back-brand {
    position: absolute; left: 50px; top: 95px;
    display: flex; flex-direction: column; align-items: center; text-align: center;
  }
  .back-dot {
    width: 110px; height: 110px; border-radius: 50%;
    background: var(--mark-light); margin-bottom: 18px;
  }
  .back-brand-name, .back-brand-line {
    font-size: 24px; color: var(--white); line-height: 1.15;
  }
  .service-list {
    position: absolute; left: 385px; top: 50px; list-style: none;
    font-style: italic; font-size: 18px; line-height: 37px; color: var(--white);
  }
  .service-list li::before { content: "• "; font-style: normal; }
</style>
</head>
<body>
<main class="canvas">

  <section class="card card-front" aria-label="Business card front">
    <div class="brand">
      <span class="brand-dot" aria-hidden="true"></span>
      <span class="brand-name">Harbour Pathway Advisors</span>
      <span class="brand-line">Leadership Programmes</span>
    </div>

    <div class="person">
      <h1 class="person-name">Name Surname</h1>
      <p class="person-title">manager</p>
    </div>

    <div class="rule rule-top"></div>

    <ul class="contact-list contact-lines">
      <li>+00 123 45 789
        <svg class="icon" viewBox="0 0 14 14" aria-hidden="true"><rect x="3" y="1" width="8" height="12" rx="1.5"/><rect x="4.5" y="2.5" width="5" height="7" fill="#f4f5f6"/></svg>
      </li>
      <li>+00 123 45 789
        <svg class="icon" viewBox="0 0 14 14" aria-hidden="true"><rect x="3" y="1" width="8" height="4"/><rect x="1" y="5" width="12" height="6" rx="1"/><rect x="3.5" y="9" width="7" height="4" fill="#f4f5f6" stroke="#2f4597"/></svg>
      </li>
      <li>office@yourdomain.com
        <svg class="icon" viewBox="0 0 14 14" aria-hidden="true"><rect x="1" y="3" width="12" height="8" rx="1"/><path d="M1.5 3.5 L7 8 L12.5 3.5" fill="none" stroke="#f4f5f6" stroke-width="1.2"/></svg>
      </li>
      <li>www.yourdomain.com
        <svg class="icon" viewBox="0 0 14 14" aria-hidden="true"><circle cx="7" cy="7" r="6"/><path d="M1 7h12M7 1c-3 3-3 9 0 12M7 1c3 3 3 9 0 12" fill="none" stroke="#f4f5f6" stroke-width="1"/></svg>
      </li>
    </ul>

    <div class="rule rule-mid"></div>

    <ul class="contact-list address-lines">
      <li>
        <span class="address-block">Your Address Goes Here<br>City, Country Zipcode</span>
        <svg class="icon" viewBox="0 0 14 14" aria-hidden="true" style="margin-top:22px"><path d="M7 0.5a4.5 4.5 0 0 0-4.5 4.5c0 3.4 4.5 8.5 4.5 8.5s4.5-5.1 4.5-8.5A4.5 4.5 0 0 0 7 0.5z"/><circle cx="7" cy="5" r="1.6" fill="#f4f5f6"/></svg>
      </li>
    </ul>
  </section>

  <section class="card card-back" aria-label="Business card back">
    <div class="back-brand">
      <span class="back-dot" aria-hidden="true"></span>
      <span class="back-brand-name">Harbour Pathway Advisors</span>
      <span class="back-brand-line">Leadership Programmes</span>
    </div>

    <ul class="service-list">
      <li>Organisational Development</li>
      <li>Positive Cultural Change</li>
      <li>Leadership Programmes</li>
      <li>Practical Development "Tools"</li>
      <li>Crew Rhythm Inventory</li>
      <li>360 Degree Assessments</li>
      <li>Strengths Based Training</li>
      <li>Coaching and Mentoring</li>
    </ul>
  </section>

</main>
</body>
</html>
```